TALMORK

The business want a professional looking business card. We have a scetch we will add but want the extra upgrade, and would like more suggestions for variations of our business cards.

```html
<!DOCTYPE html>
<html lang="en">
<head>
<meta charset="utf-8">
<title>TALMORK Business Card</title>
<link rel="stylesheet" href="https://fonts.googleapis.com/css2?family=Marcellus&family=Roboto:wght@300;400&display=swap">
<style>
  :root {
    --backdrop: #5e4a26;
    --card: #ffffff;
    --gold: #c4a66a;
    --gold-soft: #cdb27a;
    --shadow: rgba(0, 0, 0, 0.35);
  }
  * { margin: 0; padding: 0; box-sizing: border-box; }
  html, body { width: 1200px; height: 900px; overflow: hidden; }
  body {
    background: var(--backdrop);
    display: flex;
    align-items: center;
    justify-content: center;
    gap: 50px;
  }
  .card {
    width: 525px;
    height: 300px;
    background: var(--card);
    position: relative;
    box-shadow: 0 10px 28px var(--shadow);
    color: var(--gold);
  }

  /* Contact side */
  .card--contact { padding: 52px 0 0 48px; }
  .person-name {
    font-family: "Marcellus", serif;
    font-size: 30px;
    font-weight: 400;
    color: var(--gold);
    line-height: 1.1;
  }
  .person-role {
    font-family: "Roboto", sans-serif;
    font-weight: 300;
    font-size: 14px;
    letter-spacing: 0.02em;
    color: var(--gold-soft);
    margin-top: 6px;
  }
  .contact-list {
    list-style: none;
    margin-top: 30px;
    font-family: "Roboto", sans-serif;
    font-weight: 300;
    font-size: 18px;
    color: var(--gold);
  }
  .contact-item {
    display: flex;
    align-items: center;
    gap: 16px;
    height: 30px;
  }
  .contact-icon { width: 18px; height: 18px; flex: none; }

  /* Brand side */
  .card--brand {
    display: flex;
    flex-direction: column;
    align-items: center;
    justify-content: center;
  }
  .brand-lockup {
    display: flex;
    align-items: center;
    gap: 16px;
  }
  .brand-dot {
    width: 18px;
    height: 18px;
    border-radius: 50%;
    background: var(--gold);
  }
  .brand-name {
    font-family: "Marcellus", serif;
    font-size: 40px;
    letter-spacing: 0.28em;
    color: var(--gold);
  }
  .brand-tagline {
    font-family: "Roboto", sans-serif;
    font-weight: 400;
    font-size: 10px;
    letter-spacing: 0.5em;
    color: var(--gold-soft);
    margin-top: 10px;
  }
</style>
</head>
<body>

  <section class="card card--contact" aria-label="Contact side">
    <h1 class="person-name">Anders Vik Solberg</h1>
    <p class="person-role">CEO &amp; FOUNDER</p>
    <ul class="contact-list">
      <li class="contact-item">
        <svg class="contact-icon" viewBox="0 0 18 18" aria-hidden="true">
          <rect x="5" y="1.5" width="8" height="15" rx="1.5" fill="none" stroke="currentColor" stroke-width="1.4"/>
          <line x1="8" y1="14" x2="10" y2="14" stroke="currentColor" stroke-width="1.2"/>
        </svg>
        <span>004795550142</span>
      </li>
      <li class="contact-item">
        <svg class="contact-icon" viewBox="0 0 18 18" aria-hidden="true">
          <rect x="1.5" y="4" width="15" height="10" fill="currentColor"/>
          <polyline points="1.5,4 9,10 16.5,4" fill="none" stroke="#fff" stroke-width="1.2"/>
        </svg>
        <span>talmork.llc@postmail.com</span>
      </li>
      <li class="contact-item">
        <svg class="contact-icon" viewBox="0 0 18 18" aria-hidden="true">
          <circle cx="9" cy="9" r="7.5" fill="none" stroke="currentColor" stroke-width="1.2"/>
          <ellipse cx="9" cy="9" rx="3.4" ry="7.5" fill="none" stroke="currentColor" stroke-width="1"/>
          <line x1="1.5" y1="9" x2="16.5" y2="9" stroke="currentColor" stroke-width="1"/>
          <line x1="3" y1="5.2" x2="15" y2="5.2" stroke="currentColor" stroke-width="0.9"/>
          <line x1="3" y1="12.8" x2="15" y2="12.8" stroke="currentColor" stroke-width="0.9"/>
        </svg>
        <span>www.talmork.llc</span>
      </li>
    </ul>
  </section>

  <section class="card card--brand" aria-label="Brand side">
    <div class="brand-lockup">
      <span class="brand-dot" aria-hidden="true"></span>
      <span class="brand-name">TALMORK</span>
    </div>
    <p class="brand-tagline">SINCE 2026</p>
  </section>

</body>
</html>
```